Grovecraft Lip Balm. It is formulated with men in mind but other people certainly can use it.

The over arching name of the project is Tharn - which needs to be in the label somewhere, but Grovecraft is the title.
It would be for a round jar container.
It is out of promoting products for men to open discussion about health issues that men often not talk about. As each product is created it will have a message to men about the health issue and where to find information, seek help or just be able to talk about it.
I would like darker colours (black) as the base but using other colours to
for the wording and design.
I am open to ideas on the layout, I have included some ideas, and also some of my own labelling ideas that I have worked on. I do like the carbon fibre background look that I have for my tharn label. I have also included my wevnu label with some colour ideas.
I also was wondering about making it a after tattoo balm so that it can also be used as a lip balm as well…two for the price of one..basically the same ingredients are used.
They may change the look of the intended artwork..but I leave it in your skill full hands.
My number is +61498152073. You can txt me if you need some clarification.
Thank you
Kind regards and blessings

Target Market(s)

Target market is men of all ages as they can all be affected by one health issue or another at different times of life

Industry/Entity Type

Healthcare and beauty

Font styles to use
Sans Serif
Decorative

Requirements
Must have
• I still need to indeed to ingredients and container size.
Nice to have
• A novel and different look from the usual crowd that try to hard to look cool or funky

```html
<!DOCTYPE html>
<html lang="en">
<head>
<meta charset="utf-8">
<title>Tharn · Grovecraft Lip Balm · Jar Labels</title>
<link rel="stylesheet" href="https://fonts.googleapis.com/css2?family=Montserrat:wght@500;700&family=Oswald:wght@500&display=swap">
<style>
  :root {
    --backdrop: #5c5c5c;
    --label-black: #0c0c0c;
    --label-mid: #1e1e1e;
    --amber: #c47a22;
    --amber-deep: #9a5416;
    --silver: #d9d9d9;
    --white: #f4f4f4;
    --rule: #8a8a8a;
  }
  * { box-sizing: border-box; margin: 0; padding: 0; }
  html, body { width: 1200px; height: 900px; overflow: hidden; }
  body {
    background: var(--backdrop);
    font-family: "Montserrat", Arial, sans-serif;
    position: relative;
  }

  .texture {
    position: absolute; inset: 0;
    background: radial-gradient(ellipse at 50% 30%, #2a2a2a 0%, var(--label-mid) 30%, var(--label-black) 70%);
  }

  .brand-name {
    font-family: "Montserrat", Arial, sans-serif;
    font-weight: 700;
    color: var(--silver);
    letter-spacing: 1px;
    text-align: center;
  }
  .product-title {
    font-family: "Oswald", "Arial Narrow", sans-serif;
    font-weight: 500;
    color: var(--amber);
    text-transform: uppercase;
    letter-spacing: 3px;
    text-align: center;
    line-height: 1;
  }
  .product-type {
    display: flex; align-items: center; justify-content: center; gap: 14px;
    font-weight: 700; color: var(--white); text-transform: uppercase;
  }
  .product-type::before, .product-type::after {
    content: ""; height: 1px; background: var(--rule);
  }

  /* Round lid label */
  .lid-label {
    position: absolute; left: 60px; top: 190px;
    width: 520px; height: 520px; border-radius: 50%;
    overflow: hidden; background: var(--label-black);
  }
  .lid-label .texture { border-radius: 50%; }
  .lid-ring {
    position: absolute; inset: 13px; border-radius: 50%;
    border: 2px solid var(--amber);
  }
  .lid-label .brand-name { position: absolute; top: 150px; width: 100%; font-size: 58px; }
  .lid-label .product-title { position: absolute; top: 232px; width: 100%; font-size: 78px; }
  .lid-label .product-type { position: absolute; top: 330px; width: 100%; font-size: 15px; letter-spacing: 9px; }
  .lid-label .product-type::before, .lid-label .product-type::after { width: 86px; }
  .lid-volume {
    position: absolute; top: 438px; width: 100%; text-align: center;
    font-weight: 700; font-size: 25px; color: var(--white);
  }

  /* Jar wrap label */
  .wrap-label {
    position: absolute; left: 630px; top: 280px;
    width: 520px; height: 340px; overflow: hidden;
    background: var(--label-black);
  }
  .wrap-label .brand-name { position: absolute; top: 32px; width: 100%; font-size: 44px; }
  .wrap-label .product-title { position: absolute; top: 100px; width: 100%; font-size: 62px; }
  .wrap-label .product-type { position: absolute; top: 186px; width: 100%; font-size: 12px; letter-spacing: 8px; }
  .wrap-label .product-type::before, .wrap-label .product-type::after { width: 74px; }

  .claims {
    position: absolute; top: 218px; width: 100%;
    display: flex; justify-content: center; align-items: center; gap: 22px;
  }
  .claim {
    width: 36px; height: 36px; border-radius: 50%;
    border: 1.5px solid var(--amber);
    display: flex; flex-direction: column; align-items: center; justify-content: center;
    color: var(--white); font-size: 4.5px; font-weight: 700; line-height: 1.1; text-align: center;
  }
  .claim strong { color: var(--amber); font-size: 7px; }
  .claim svg { width: 12px; height: 10px; }
  .claim-divider { width: 1px; height: 38px; background: var(--rule); }

  .band-silver {
    position: absolute; left: 0; right: 0; top: 307px; height: 3px;
    background: linear-gradient(90deg, #8c8c8c, #efefef 50%, #8c8c8c);
  }
  .band-amber {
    position: absolute; left: 0; right: 0; top: 318px; height: 6px;
    background: linear-gradient(90deg, var(--amber-deep), var(--amber) 50%, var(--amber-deep));
  }
  .volume-tab {
    position: absolute; left: 50%; top: 291px; transform: translateX(-50%);
    width: 96px; height: 27px;
    background: var(--amber);
    clip-path: polygon(8% 0, 92% 0, 100% 100%, 0 100%);
    display: flex; align-items: center; justify-content: center;
    font-weight: 700; font-size: 15px; color: var(--label-black);
  }
</style>
</head>
<body>

  <section class="lid-label" aria-label="Round lid label">
    <div class="texture" role="img" aria-label="Dark carbon fibre hexagon texture"></div>
    <div class="lid-ring"></div>
    <div class="brand-name">THARN</div>
    <h1 class="product-title">Grovecraft</h1>
    <div class="product-type">Lip Balm</div>
    <div class="lid-volume">50ML</div>
  </section>

  <section class="wrap-label" aria-label="Jar side label">
    <div class="texture" role="img" aria-label="Dark carbon fibre hexagon texture"></div>
    <div class="brand-name">THARN</div>
    <h2 class="product-title">Grovecraft</h2>
    <div class="product-type">Lip Balm</div>

    <div class="claims">
      <div class="claim">
        <svg viewBox="0 0 12 10" aria-hidden="true"><path d="M2 2 L6 9 L10 1" fill="none" stroke="#c47a22" stroke-width="1.3"/></svg>
        <span>VEGAN<br>FRIENDLY</span>
      </div>
      <div class="claim-divider"></div>
      <div class="claim"><strong>100%</strong><span>NATURAL</span></div>
      <div class="claim-divider"></div>
      <div class="claim">
        <svg viewBox="0 0 12 10" aria-hidden="true"><path d="M6 10 V4 M6 5 C3 5 2 3 2 1 C4 1 6 2 6 5 C6 2 8 1 10 1 C10 3 9 5 6 5" fill="none" stroke="#c47a22" stroke-width="1"/></svg>
        <span>NON-GMO</span>
      </div>
    </div>

    <div class="band-silver"></div>
    <div class="band-amber"></div>
    <div class="volume-tab">50ML</div>
  </section>

</body>
</html>
```